Advanced Therapeutic Massage Therapist

I need a business card advertising my massage services as an advanced therapeutic massage therapist. I offer advanced therapeutic massage, swedish and deep tissue. I want to create a simple, professional and feminine card. I like bright colours and creativity.

I prefer a bold and experimental approach rather than something status-quo. A card to suggest therapeutic healing through dynamic massage. Motifs, shapes or layout which suggest movement and flow.
Updates

Target Market(s)

Everybody!

Industry/Entity Type

Health And Wellness

Contact Information for Business Card

The card should include:
My name, logo, services offered and my contact details.

Sláine Dunleavy
Massage Therapist

- Swedish - Deep Tissue - Advanced Therapeutic

Phone: (+353) 87 216 4093
Email: regenerate@slainedunleavy-example.com
Website: www.slainedunlevy-example.com

Font styles to use
Serif
Sans Serif
Decorative
Script

Colors

Designer to choose colors to be used in the design.

Requirements
Must have
• An example may contain something like this, yet concise:
• "Sláine Dunleavy
• Massage Therapist
• - Swedish - Deep Tissue - Advanced Therapeutic"
Nice to have
• This sentence is optional:
• Imagery such as a logo or symbol. I have attached a file containing a logo I had produced however the name is incorrect now as it is "Sláine" not "Nelly". It could be edited to change it to Sláine.
• I have sent the file as .psd .jpg. .pdf and .png
• I like when the card conveys energy, movement, pressure points, flow etc.
• I just like the designer to follow their own style and ideas. I like bright colours but must have a lot of a base colour to offset it. I really prefer them to follow their own inspiration. That is my preference.
Should not have
• Pine trees, non-native trees to Britain and Ireland, exotic flowers or animals that are not native to Britain and Ireland.
• I don't like brown as the background colour of the card.
• The cars shouldn't look like a wedding invitation i.e too many floral type designs.

```html
<!DOCTYPE html>
<html lang="en">
<head>
<meta charset="utf-8">
<title>Sláine Dunleavy – Massage Therapist</title>
<link rel="stylesheet" href="https://fonts.googleapis.com/css2?family=Pinyon+Script&family=Crimson+Text:ital,wght@0,400;0,600;1,400&display=swap">
<style>
  :root{
    --page:#2a2a2a;
    --teal:#a9ddd0;
    --teal-light:#c9ece2;
    --teal-deep:#7fc8b6;
    --gold:#b9772e;
    --gold-light:#d9a556;
    --panel:#fffdfb;
    --ink:#2b2b2b;
    --accent:#6cbfa9;
  }
  *{box-sizing:border-box;margin:0;padding:0}
  html,body{width:1200px;height:1200px;overflow:hidden}
  body{background:var(--page);display:flex;flex-direction:column;align-items:center;justify-content:center;gap:44px;font-family:"Crimson Text",serif;color:var(--ink)}
  .card{position:relative;width:880px;height:500px;border-radius:30px;overflow:hidden}
  .card__pattern{position:absolute;inset:0;background:
      radial-gradient(circle at 20% 25%, var(--gold-light) 0 3%, transparent 18%),
      radial-gradient(circle at 80% 75%, var(--gold) 0 2%, transparent 16%),
      radial-gradient(circle at 85% 15%, var(--gold-light) 0 2%, transparent 14%),
      radial-gradient(circle at 10% 85%, var(--gold) 0 2%, transparent 14%),
      linear-gradient(135deg, var(--teal-light), var(--teal) 50%, var(--teal-deep));}
  .card__panel{position:absolute;inset:62px 70px;background:var(--panel);display:flex;flex-direction:column;align-items:center;justify-content:center;text-align:center;box-shadow:0 0 0 1px rgba(0,0,0,.04)}
  .name{font-family:"Pinyon Script",cursive;font-size:52px;line-height:1;color:var(--ink)}
  .role{font-size:20px;letter-spacing:1px;margin-top:6px}
  .contact{margin-top:30px;font-size:19px;display:flex;flex-direction:column;gap:10px;align-items:center}
  .contact__row{display:flex;align-items:center;gap:10px}
  .icon{width:18px;height:18px;fill:var(--accent)}
  .divider{color:#888}
  .services{margin-top:26px;font-size:19px;display:flex;gap:14px;align-items:center}
  .star{color:var(--accent);font-size:16px}
  .brand{display:flex;align-items:center;gap:16px}
  .brand__dot{width:74px;height:74px;border-radius:50%;background:radial-gradient(circle,var(--teal-light),var(--teal-deep))}
  .brand__name{font-size:30px;color:#8a8a8a}
  .tagline{margin-top:22px;font-style:italic;font-size:20px;line-height:1.35}
</style>
</head>
<body>
  <section class="card card--contact">
    <div class="card__pattern" role="img" aria-label="Teal background with flowing gold scroll ornament"></div>
    <div class="card__panel">
      <h1 class="name">Sláine Dunleavy</h1>
      <p class="role">Massage Therapist</p>
      <div class="contact">
        <div class="contact__row">
          <svg class="icon" viewBox="0 0 24 24" aria-hidden="true"><path d="M6.6 10.8a15 15 0 0 0 6.6 6.6l2.2-2.2c.3-.3.7-.4 1-.2 1.1.4 2.3.6 3.6.6.6 0 1 .4 1 1V20c0 .6-.4 1-1 1A17 17 0 0 1 3 4c0-.6.4-1 1-1h3.5c.6 0 1 .4 1 1 0 1.3.2 2.5.6 3.6.1.3 0 .7-.2 1z"/></svg>
          <span>(+353) 87 216 4093</span>
          <span class="divider">|</span>
          <svg class="icon" viewBox="0 0 24 24" aria-hidden="true"><path d="M3 5h18v14H3z M3 5l9 7 9-7" fill="none" stroke="#6cbfa9" stroke-width="2"/></svg>
          <span>regenerate@slainedunleavy-example.com</span>
        </div>
        <div class="contact__row">
          <svg class="icon" viewBox="0 0 24 24" aria-hidden="true"><circle cx="12" cy="12" r="9" fill="none" stroke="#6cbfa9" stroke-width="2"/><path d="M3 12h18M12 3c3 3 3 15 0 18M12 3c-3 3-3 15 0 18" fill="none" stroke="#6cbfa9" stroke-width="1.5"/></svg>
          <span>www.slainedunlevy-example.com</span>
        </div>
      </div>
      <p class="services"><span>Swedish</span><span class="star">★</span><span>Deep Tissue</span><span class="star">★</span><span>Advanced Therapeutic</span></p>
    </div>
  </section>

  <section class="card card--brand">
    <div class="card__pattern" role="img" aria-label="Teal background with flowing gold scroll ornament"></div>
    <div class="card__panel">
      <div class="brand">
        <span class="brand__dot"></span>
        <span class="brand__name">Nelly Dunleavy</span>
      </div>
      <p class="tagline">ATEB qualified specialising in<br>advanced therapeutic and deep tissue massage</p>
    </div>
  </section>
</body>
</html>
```